Technology, Futuristic Innovation & Artificial Intelligence

I am looking for something with Artificial Intelligence DNA strands....
Blue, black, with white dna strands........I like clean, crisp, professional and not busy look.................................................................................................................................................................................................................................................................................................................................................................................. Thanks!

Target Market(s)

Engineers and United States Government Contractors

Industry/Entity Type

Engineering

Contact Information for Business Card

I've uploaded my logo the certification logo.

Font styles to use
Serif

Colors
3176b5
33a6d7
ffffff

Requirements
Must have
• Name
• Title
• Address
• Phone number
• website name
• certification logo
Nice to have
• Something with Artificial Intelligence DNA strands......
• **Please note it would be nice to have the business card 3D or textured with raised images. Thanks
Should not have
• Please no feminine flowery designs....this is an engineering firm

```html
<!DOCTYPE html>
<html lang="en">
<head>
<meta charset="utf-8">
<title>Vantrex Business Card</title>
<link rel="stylesheet" href="https://fonts.googleapis.com/css2?family=Work+Sans:wght@400;500&family=Oswald:wght@400&family=Roboto+Condensed:wght@700&display=swap">
<style>
  :root {
    --page: #e7e4df;
    --navy-deep: #05061a;
    --navy: #16195a;
    --indigo: #24297c;
    --glow: #33a6d7;
    --steel: #3176b5;
    --white: #ffffff;
    --ink: #1b1b1b;
    --silver: #d9dde3;
    --gold: #e0b64a;
  }
  * { box-sizing: border-box; margin: 0; padding: 0; }
  html, body { width: 1200px; height: 930px; overflow: hidden; }
  body { background: var(--page); position: relative; font-family: "Work Sans", sans-serif; }

  .card {
    position: absolute; left: 278px; width: 645px; height: 368px;
    border-radius: 22px; overflow: hidden;
    box-shadow: 0 6px 14px rgba(0,0,0,.25);
  }
  .card--front { top: 76px; }
  .card--back { top: 486px; }

  .circuit-field {
    position: absolute; inset: 0;
    background:
      radial-gradient(circle at 40% 20%, rgba(51,166,215,.35), transparent 35%),
      radial-gradient(circle at 75% 70%, rgba(49,118,181,.3), transparent 40%),
      linear-gradient(90deg, var(--navy-deep) 0%, var(--navy) 45%, var(--indigo) 100%);
  }

  .info-band {
    position: absolute; left: 0; right: 0; top: 94px; height: 179px;
    background: var(--white);
  }
  .brand-name {
    position: absolute; font-family: "Work Sans", sans-serif; font-weight: 500;
    letter-spacing: 4px; display: flex; align-items: center; gap: 12px;
  }
  .brand-mark { display: block; background: var(--steel); }
  .info-band .brand-name { left: 48px; top: 70px; font-size: 36px; color: var(--ink); }
  .info-band .brand-mark { width: 18px; height: 18px; }

  .divider { position: absolute; left: 331px; top: 16px; width: 2px; height: 148px; background: var(--ink); }

  .contact { position: absolute; left: 362px; top: 8px; color: var(--ink); }
  .contact__name { font-size: 24px; font-weight: 400; letter-spacing: 1px; line-height: 1.2; }
  .contact__title { font-size: 15px; margin-top: 2px; letter-spacing: .5px; }
  .contact__address { font-size: 16px; line-height: 20px; margin-top: 10px; letter-spacing: .3px; }
  .contact__lines { list-style: none; margin-top: 7px; font-size: 16px; line-height: 20px; letter-spacing: .3px; }
  .contact__lines li { display: flex; align-items: center; gap: 10px; margin-left: -1px; }
  .contact__lines svg { width: 9px; height: 9px; flex: none; }

  .naics {
    position: absolute; left: 0; right: 0; top: 292px; text-align: center;
    font-family: "Oswald", sans-serif; font-size: 22px; line-height: 29px; color: var(--white);
  }

  .card--back .brand-name { left: 0; right: 0; top: 140px; justify-content: center; font-size: 56px; color: var(--silver); letter-spacing: 8px; }
  .card--back .brand-mark { width: 26px; height: 26px; }
  .tagline {
    position: absolute; left: 133px; right: 132px; top: 224px;
    display: flex; align-items: center; gap: 6px;
    font-family: "Roboto Condensed", sans-serif; font-weight: 700; font-size: 15px; color: var(--white);
  }
  .tagline::before { content: ""; flex: 1; height: 2px; background: var(--white); }
  .certification-badge {
    position: absolute; left: 312px; top: 272px; width: 68px; height: 68px;
    border-radius: 50%; background: var(--steel); border: 4px solid var(--gold);
  }
</style>
</head>
<body>

<section class="card card--front">
  <div class="circuit-field" role="img" aria-label="Glowing blue circuit board pattern on deep navy"></div>
  <div class="info-band">
    <div class="brand-name"><span class="brand-mark"></span>VANTREX</div>
    <div class="divider"></div>
    <div class="contact">
      <h1 class="contact__name">DANA WHITLOCK</h1>
      <p class="contact__title">CEO</p>
      <p class="contact__address">1820 Marlowe Lane<br>Brookfield, SC 29031</p>
      <ul class="contact__lines">
        <li><svg viewBox="0 0 10 10"><path d="M2 1 L4 1 L4.6 3 L3.4 3.8 Q4.4 6 6.2 6.8 L7 5.6 L9 6.2 L9 8 Q5 9 2 5 Q1 3 2 1Z" fill="#1b1b1b"/></svg>555.204.7710</li>
        <li><svg viewBox="0 0 10 10"><rect x="0.7" y="2" width="8.6" height="6" fill="none" stroke="#1b1b1b"/><path d="M0.7 2 L5 5.5 L9.3 2" fill="none" stroke="#1b1b1b"/></svg>dwhitlock@vantrex.org</li>
        <li><svg viewBox="0 0 10 10" fill="none" stroke="#1b1b1b" stroke-width=".8"><circle cx="5" cy="5" r="4.2"/><ellipse cx="5" cy="5" rx="1.8" ry="4.2"/><path d="M0.8 5 H9.2 M1.5 3 H8.5 M1.5 7 H8.5"/></svg>www.vantrex.org</li>
      </ul>
    </div>
  </div>
  <p class="naics">NAICS: 5412-20/30/60, 5417-12/15/19, 5418-40<br>5612-20, 5614-21/30/40, 5617-30</p>
</section>

<section class="card card--back">
  <div class="circuit-field" role="img" aria-label="Glowing blue circuit board pattern on deep navy"></div>
  <div class="brand-name"><span class="brand-mark"></span>VANTREX</div>
  <p class="tagline">ENGINEERING WHAT COMES NEXT</p>
  <div class="certification-badge" role="img" aria-label="Verified federal contractor certification badge"></div>
</section>

</body>
</html>
```